Erstellung eines Polizeiwimpels für Kinder
Zielgruppe
Wir stellen Fahrradwimpel für Kinder her. Hier finden Sie unsere Produkte: https://www.kaufhalle-wiro.de/laden/regal/58203917462
Aufgabenstellung
Wir möchten einen 'Polizeiwimpel' für Kinder herstellen.
Wenn möglich, nur eine Farbe verwenden (reduziert Kosten in der Produktion). Der Hintergrund soll 'Polizei Blau' sein.
Wimpelgröße: 17,5 cm X 32 cm X 32cm (Dreieckig)
Ich habe ein selbst erstelltes Design hochgeladen. Es soll den Schriftzug 'Polizei' enthalten und evtl. noch 'Polizei Symbole', die Jungs (und ihre Eltern) ansprechen. (Pistole, Sheriffstern, etc.) Das offizielle Wappen oder andere Hoheitssymbole dürfen wir allerdings nicht verwenden.

```html
<!DOCTYPE html>
<html lang="de">
<head>
<meta charset="utf-8">
<title>Polizeiwimpel für Kinder</title>
<link rel="stylesheet" href="https://fonts.googleapis.com/css2?family=Arimo:wght@700&display=swap">
<style>
  :root {
    --police-blue: #1670b8;
    --print-grey: #dcdcdc;
    --page: #ffffff;
  }
  html, body {
    margin: 0;
    padding: 0;
    width: 1200px;
    height: 657px;
    overflow: hidden;
    background: var(--page);
  }
  .pennant {
    display: block;
    width: 1200px;
    height: 657px;
  }
  .pennant__field { fill: var(--police-blue); }
  .pennant__border {
    fill: none;
    stroke: var(--print-grey);
    stroke-width: 22;
    stroke-dasharray: 64 30;
  }
  .pennant__emblem { fill: var(--print-grey); }
  .pennant__title {
    fill: var(--print-grey);
    font-family: "Arimo", Arial, sans-serif;
    font-weight: 700;
    font-size: 172px;
  }
  .pennant__web {
    fill: var(--print-grey);
    font-family: "Arimo", Arial, sans-serif;
    font-weight: 700;
    font-size: 13px;
  }
</style>
</head>
<body>
<svg class="pennant" viewBox="0 0 1200 657" xmlns="http://www.w3.org/2000/svg">
  <polygon class="pennant__field" points="0,0 1195,323 0,657"/>
  <polyline class="pennant__border" points="8,30 1085,320"/>
  <polyline class="pennant__border" points="8,627 1085,326"/>
  <g transform="rotate(-14.5 190 300)">
    <rect class="pennant__emblem" x="95" y="240" width="200" height="120" rx="40"
          role="img" aria-label="Polizeimütze mit Stern"/>
  </g>
  <text class="pennant__title" x="52" y="522" textLength="700" lengthAdjust="spacingAndGlyphs"
        transform="rotate(-14.5 52 522)">POLIZEI</text>
  <text class="pennant__web" x="752" y="380" transform="rotate(-14.5 752 380)">www.radwimpel-wiro.bike</text>
</svg>
</body>
</html>
```